Business card for start up company

SIMPLE, CLEAN, FRESH, MODERN, SOPHISTICATED. professional. experienced, easy to deal with, expert in the field. local ethics.

professional business card for Forge Mark Works. using company logo supplied and images.

GENERAL ENGINEERING - MACHINING - WELDING - MAINTENANCE

Forge Mark Works Ltd is a locally owned mechanical engineering company that specialises in general and mechanical engineering, as well as steel fabrication, welding, repairs and maintenance.

We specialise in the design, welding, fabrication and installation of stainless and mild steel fabrications. We service commercial and residential clients; large or small projects; production line or one off designs.

We have built a solid reputation for quality and service for our machinery and engineering work around Northland NZ. For innovative, cost effective and efficient engineering solutions, to suit a wide range of commercial, residential and rural applications.

Reason: doing on behalf. went away on holiday

Target Market(s)

boat builders. DIY. industrial. RESIDENTIAL. COMMERCIAL

Industry/Entity Type

Mechanical Engineering

Contact Information for Business Card

CONTACT / SERVICES SIDE
Forge Mark Works Ltd.
Design | Machining | Welding | Fabrication | Installation | Maintenance
www.forgemarkworks-example.co.nz
grant@forgemarkworks-example.co.nz

Font styles to use
Serif

Colors

Designer to choose colors to be used in the design.

Requirements
Must have
• LOGO ONLY WITH NEGATIVE SPACE ON FRONT SIDE
• services and contact side , either use stock photos (supplied) as background or background supplied in logo photos.
Nice to have
• use the symbol icon in logo on contact/ services side, , enlarged, transparent and faded into the background with text over the top on the
• Design | Machining | Welding | Fabrication | Installation | Maintenance
• the above services to be subtle, along the bottom edge of the services side. can i also have another proof with eh above services featuring on the bottom edge of the LOGO FRONT side to see if the text looks better with or without.
Should not have
• crowded, busy, different fonts. different casing.
• use fonts in the logo files designer to make font decision.

```html
<!DOCTYPE html>
<html lang="en">
<head>
<meta charset="utf-8">
<title>Forge Mark Works Ltd. – Business Card</title>
<link rel="stylesheet" href="https://fonts.googleapis.com/css2?family=Archivo:wght@500;700&family=Tinos&display=swap">
<style>
  :root {
    --backdrop: #2b2b2d;
    --card-silver-light: #f4f4f5;
    --card-silver-mid: #dcdcde;
    --card-silver-dark: #c6c6c9;
    --ink-dark: #3a3a3c;
    --ink-soft: #8c8c90;
    --accent-orange: #e2622a;
    --divider-white: #ffffff;
    --photo-gears: #8a8c8f;
    --photo-machining: #6d6f73;
    --photo-toolbelt: #4a5f86;
    --photo-welding: #23408a;
  }
  * { margin: 0; padding: 0; box-sizing: border-box; }
  html, body {
    width: 1200px;
    height: 880px;
    overflow: hidden;
    background: var(--backdrop);
  }
  .sheet {
    width: 1200px;
    height: 880px;
    display: flex;
    flex-direction: column;
    align-items: center;
    justify-content: center;
    gap: 40px;
  }
  .card {
    width: 660px;
    height: 377px;
    border-radius: 22px;
    overflow: hidden;
    position: relative;
    box-shadow: 0 10px 28px rgba(0,0,0,0.45);
  }
  .card--photos svg { display: block; width: 100%; height: 100%; }

  .card--contact {
    background:
      linear-gradient(115deg, transparent 55%, rgba(255,255,255,0.55) 68%, transparent 80%),
      linear-gradient(160deg, var(--card-silver-light) 0%, var(--card-silver-mid) 55%, var(--card-silver-dark) 100%);
    padding: 70px 48px 0 48px;
  }
  .brand {
    display: flex;
    align-items: center;
    gap: 18px;
  }
  .brand__square {
    width: 50px;
    height: 50px;
    background: var(--ink-dark);
    flex: none;
  }
  .brand__name {
    font-family: "Archivo", sans-serif;
    font-weight: 700;
    font-size: 40px;
    letter-spacing: 0.5px;
    color: var(--ink-dark);
    text-transform: uppercase;
  }
  .company-name {
    margin-top: 78px;
    font-family: "Archivo", sans-serif;
    font-weight: 700;
    font-size: 25px;
    color: var(--ink-dark);
    text-transform: uppercase;
  }
  .contact-list {
    list-style: none;
    margin-top: 10px;
    font-family: "Tinos", serif;
    font-size: 15px;
    color: var(--ink-dark);
  }
  .contact-list li {
    display: flex;
    align-items: center;
    gap: 8px;
    line-height: 22px;
  }
  .contact-list svg { width: 16px; height: 16px; flex: none; }
  .services {
    margin-top: 8px;
    font-family: "Tinos", serif;
    font-size: 15px;
    color: var(--ink-dark);
    letter-spacing: 0.2px;
  }
</style>
</head>
<body>
<main class="sheet">

  <section class="card card--photos">
    <svg viewBox="0 0 660 377" xmlns="http://www.w3.org/2000/svg">
      <polygon points="0,0 290,0 230,377 0,377" fill="var(--photo-gears)" role="img" aria-label="Photo of meshing steel gears"/>
      <polygon points="290,0 660,0 660,100 270,130" fill="var(--photo-machining)" role="img" aria-label="Photo of a lathe machining metal"/>
      <polygon points="270,130 660,100 660,377 230,377" fill="var(--photo-toolbelt)" role="img" aria-label="Photo of a tradesman wearing a tool belt"/>
      <polygon points="0,250 250,250 230,377 0,377" fill="var(--photo-welding)" role="img" aria-label="Photo of a welder at work with sparks"/>
      <line x1="290" y1="0" x2="230" y2="377" stroke="var(--divider-white)" stroke-width="8"/>
      <line x1="270" y1="130" x2="660" y2="100" stroke="var(--divider-white)" stroke-width="8"/>
      <line x1="0" y1="250" x2="250" y2="250" stroke="var(--divider-white)" stroke-width="8"/>
    </svg>
  </section>

  <section class="card card--contact">
    <div class="brand">
      <span class="brand__square"></span>
      <span class="brand__name">Forge Mark Works</span>
    </div>
    <h1 class="company-name">Forge Mark Works Ltd.</h1>
    <ul class="contact-list">
      <li>
        <svg viewBox="0 0 16 16" aria-hidden="true">
          <circle cx="8" cy="8" r="8" fill="var(--accent-orange)"/>
          <circle cx="8" cy="8" r="4.5" fill="none" stroke="#fff" stroke-width="1"/>
          <ellipse cx="8" cy="8" rx="2" ry="4.5" fill="none" stroke="#fff" stroke-width="1"/>
          <line x1="3.5" y1="8" x2="12.5" y2="8" stroke="#fff" stroke-width="1"/>
        </svg>
        www.forgemarkworks-example.co.nz
      </li>
      <li>
        <svg viewBox="0 0 16 16" aria-hidden="true">
          <circle cx="8" cy="8" r="8" fill="var(--accent-orange)"/>
          <rect x="4" y="5" width="8" height="6" fill="none" stroke="#fff" stroke-width="1"/>
          <polyline points="4,5 8,8.5 12,5" fill="none" stroke="#fff" stroke-width="1"/>
        </svg>
        grant@forgemarkworks-example.co.nz
      </li>
    </ul>
    <p class="services">Design | Machining | Welding | Fabrication | Installation | Maintenance</p>
  </section>

</main>
</body>
</html>
```